Business Card Design

New business card design

Target Market(s)

Residential & Commercial Property Managers

Industry/Entity Type

Plumbing Services

Contact Information for Business Card

Name - Rowan Keddle, title - Director, Phone Number - 0431 286 517, email - rowan@tbk-plumbing.com.au, Company ABN - 73 215 904 386,

Font styles to use
Sans Serif

Colors
0054AA
0677BA
7BADD7
CADEEF
E8F1F8

```html
<!DOCTYPE html>
<html lang="en">
<head>
<meta charset="utf-8">
<title>TBK Plumbing Services – Business Card</title>
<link href="https://fonts.googleapis.com/css2?family=Roboto:wght@300;400;700&display=swap" rel="stylesheet">
<style>
  :root {
    --bg: #ececec;
    --card-white: #ffffff;
    --brand-blue: #0aa8e9;
    --brand-blue-light: #4cc3f2;
    --brand-blue-deep: #0677ba;
    --ink-dark: #1f2327;
    --ink-text: #3a3d40;
    --rule: #9a9ea2;
  }
  * { margin: 0; padding: 0; box-sizing: border-box; }
  html, body { width: 1200px; height: 900px; overflow: hidden; }
  body {
    background: var(--bg);
    font-family: "Roboto", Arial, sans-serif;
    position: relative;
  }
  .card {
    position: absolute;
    left: 280px;
    width: 640px;
    height: 360px;
    border-radius: 26px;
    overflow: hidden;
    box-shadow: 0 10px 30px rgba(0,0,0,.12);
  }
  .card--front { top: 50px; background: var(--card-white); }
  .card--back { top: 480px; background: var(--brand-blue); }

  .wordmark {
    position: absolute;
    display: flex;
    align-items: center;
    gap: 12px;
    font-weight: 300;
    white-space: nowrap;
  }
  .wordmark__dot { border-radius: 50%; flex: none; }
  .card--front .wordmark { left: 44px; top: 110px; font-size: 27px; color: var(--ink-dark); }
  .card--front .wordmark__dot { width: 16px; height: 16px; background: var(--brand-blue); }
  .card--back .wordmark { left: 60px; top: 110px; font-size: 36px; color: var(--card-white); }
  .card--back .wordmark__dot { width: 20px; height: 20px; background: var(--card-white); }

  .divider {
    position: absolute;
    left: 360px; top: 70px;
    width: 1px; height: 150px;
    background: var(--rule);
  }
  .contact { position: absolute; left: 384px; top: 80px; color: var(--ink-text); }
  .contact__name {
    font-weight: 700; font-size: 24px; color: var(--brand-blue);
    text-transform: uppercase; letter-spacing: .2px;
  }
  .contact__title { font-size: 17px; margin-top: 2px; }
  .contact__line {
    display: flex; align-items: center; gap: 7px;
    font-size: 17px; margin-top: 8px; white-space: nowrap;
  }
  .contact__line svg { width: 14px; height: 14px; flex: none; }
  .contact__line:first-of-type { margin-top: 12px; }

  .abn-band {
    position: absolute; left: 0; top: 262px;
    width: 478px; height: 36px;
    background: var(--ink-dark);
    display: flex; align-items: center; justify-content: flex-end;
    padding-right: 40px;
    font-size: 17px; color: #e8e8e8;
  }
  .abn-band__label { color: var(--brand-blue); margin-right: 6px; }
  .accent-strip {
    position: absolute; left: 0; top: 306px;
    width: 100%; height: 10px; background: var(--brand-blue);
  }
  .accent-block {
    position: absolute; left: 478px; top: 262px;
    width: 162px; height: 54px; background: var(--brand-blue);
  }
  .accent-circle {
    position: absolute; left: 452px; top: 254px;
    width: 52px; height: 52px; border-radius: 50%;
    background: var(--card-white);
    display: flex; align-items: center; justify-content: center;
  }
  .accent-circle span {
    width: 34px; height: 34px; border-radius: 50%; background: var(--brand-blue);
  }

  .back-circle {
    position: absolute; left: 400px; top: 140px;
    width: 300px; height: 300px; border-radius: 50%;
    background: linear-gradient(150deg, var(--brand-blue-light), var(--brand-blue-deep));
    opacity: .55;
  }
</style>
</head>
<body>
  <section class="card card--front" aria-label="Business card front">
    <div class="wordmark"><span class="wordmark__dot"></span>TBK Plumbing Services</div>
    <div class="divider"></div>
    <div class="contact">
      <div class="contact__name">Rowan Keddle</div>
      <div class="contact__title">Director</div>
      <div class="contact__line">
        <svg viewBox="0 0 16 16" aria-hidden="true"><path fill="#0aa8e9" d="M3.5 1.5l2.5 0 1.2 3.2-1.6 1.1a8 8 0 0 0 4.6 4.6l1.1-1.6 3.2 1.2v2.5c0 .8-.7 1.5-1.5 1.5C7 14 2 9 2 3c0-.8.7-1.5 1.5-1.5z"/></svg>
        0431 286 517
      </div>
      <div class="contact__line">
        <svg viewBox="0 0 16 16" aria-hidden="true"><rect x="1" y="3" width="14" height="10" rx="1.5" fill="#0aa8e9"/><path d="M1.5 4l6.5 5 6.5-5" stroke="#fff" stroke-width="1.4" fill="none"/></svg>
        rowan@tbk-plumbing.com.au
      </div>
    </div>
    <div class="abn-band"><span class="abn-band__label">ABN:</span>73 215 904 386</div>
    <div class="accent-strip"></div>
    <div class="accent-block"></div>
    <div class="accent-circle"><span></span></div>
  </section>

  <section class="card card--back" aria-label="Business card back">
    <div class="back-circle"></div>
    <div class="wordmark"><span class="wordmark__dot"></span>TBK Plumbing Services</div>
  </section>
</body>
</html>
```